Boutique custom software development company needs new business card

Our nearly 20 year old custom software development company would like to better include the fact that we are now providing Bitcoin services. These new services are B2B include education (how to acquire and securely hold Bitcoin) and integrating Bitcoin payments into existing ecommerce sites or other existing systems. Please keep the card clean and simple. Attached is our current design and some other files. vextorial.com

Target Market(s)

businesses owners interested in long term relationship

Industry/Entity Type

Custom software development and Bitcoin

Contact Information for Business Card

Dale Parker, dale@vextorial.com, vextorial.com, (888) 555-VXTRL

Font styles to use
Other font styles liked:
• monospace

Requirements
Must have
• double-sided
Nice to have
• clean and simple
Should not have
• physical address

```html
<!DOCTYPE html>
<html lang="en">
<head>
<meta charset="utf-8">
<title>Vextorial business card</title>
<link rel="stylesheet" href="https://fonts.googleapis.com/css2?family=Montserrat:wght@400;500;600;700;800&display=swap">
<style>
  :root {
    --brand-blue: #3d74ba;
    --brand-orange: #f07f1e;
    --paper: #ffffff;
    --ink: #3a3a3a;
    --backdrop: #d2d1ce;
  }
  * { margin: 0; padding: 0; box-sizing: border-box; }
  html, body {
    width: 1200px; height: 801px; overflow: hidden;
    background: var(--backdrop);
    font-family: "Montserrat", sans-serif;
  }
  .sheet {
    position: relative; width: 1200px; height: 801px;
    display: flex; align-items: center; justify-content: center; gap: 50px;
  }
  .card {
    position: relative; width: 540px; height: 309px; overflow: hidden;
    border-bottom: 3px solid var(--brand-orange);
    box-shadow: 0 10px 24px rgba(0,0,0,.18);
  }

  /* contact side */
  .card--contact { background: var(--paper); }
  .card__band {
    position: absolute; left: 0; top: 0; bottom: 0; width: 150px;
    background: var(--brand-blue);
  }
  .band__brand {
    position: absolute; left: 75px; top: 50%;
    transform: translate(-50%, -50%) rotate(-90deg);
    text-align: center; color: var(--paper); white-space: nowrap;
  }
  .band__name { font-weight: 800; font-size: 36px; letter-spacing: 1px; line-height: 1; }
  .band__tagline { font-weight: 400; font-size: 13px; margin-top: 6px; line-height: 1.2; }
  .band__services { font-weight: 600; font-size: 11px; margin-top: 4px; letter-spacing: .3px; line-height: 1.2; }

  .contact { position: absolute; left: 196px; top: 92px; color: var(--ink); }
  .contact__name { font-weight: 700; font-size: 24px; letter-spacing: 1.5px; line-height: 1; }
  .contact__first { color: var(--brand-orange); }
  .contact__last { color: var(--brand-blue); }
  .contact__role { font-size: 14px; font-weight: 500; margin-top: 4px; }
  .contact__list { list-style: none; margin-top: 26px; }
  .contact__item { display: flex; align-items: center; gap: 8px; font-size: 14px; margin-bottom: 7px; letter-spacing: .3px; }
  .contact__icon { width: 12px; height: 12px; flex: none; fill: var(--brand-blue); }

  /* brand side */
  .card--brand { background: var(--brand-blue); }
  .brand { position: absolute; left: 0; right: 0; top: 50%; transform: translateY(-50%); text-align: center; color: var(--paper); }
  .brand__name { font-weight: 800; font-size: 66px; letter-spacing: 2px; line-height: 1; }
  .brand__tagline { font-weight: 400; font-size: 24px; margin-top: 10px; line-height: 1.2; }
  .brand__services { font-weight: 600; font-size: 15px; margin-top: 14px; letter-spacing: .5px; line-height: 1.2; }
</style>
</head>
<body>
<main class="sheet">
  <section class="card card--contact" aria-label="Card back with contact details">
    <div class="card__band">
      <div class="band__brand">
        <div class="band__name">VEXTORIAL</div>
        <div class="band__tagline">developer of custom applications</div>
        <div class="band__services">Bitcoin education &amp; payments</div>
      </div>
    </div>
    <div class="contact">
      <div class="contact__name"><span class="contact__first">DALE</span> <span class="contact__last">PARKER</span></div>
      <div class="contact__role">Owner</div>
      <ul class="contact__list">
        <li class="contact__item">
          <svg class="contact__icon" viewBox="0 0 12 12" aria-hidden="true"><path d="M2.5 1 4.5 1 5.3 3.5 4 4.5Q5 7 7.5 8L8.5 6.7 11 7.5 11 9.5Q10.5 11 9 11 1 10 1 3 1 1.5 2.5 1Z"/></svg>
          (888) 555-VXTRL
        </li>
        <li class="contact__item">
          <svg class="contact__icon" viewBox="0 0 12 12" aria-hidden="true"><rect x="0.5" y="2" width="11" height="8"/><path d="M1 2.5 6 6.5 11 2.5" stroke="#fff" stroke-width="1" fill="none"/></svg>
          dale@vextorial.com
        </li>
        <li class="contact__item">
          <svg class="contact__icon" viewBox="0 0 12 12" aria-hidden="true"><circle cx="6" cy="6" r="5.5"/><path d="M0.5 6H11.5M6 0.5C3.5 3 3.5 9 6 11.5M6 0.5C8.5 3 8.5 9 6 11.5" stroke="#fff" stroke-width=".8" fill="none"/></svg>
          www.vextorial.com
        </li>
      </ul>
    </div>
  </section>

  <section class="card card--brand" aria-label="Card front with company name">
    <div class="brand">
      <div class="brand__name">VEXTORIAL</div>
      <div class="brand__tagline">developer of custom applications</div>
      <div class="brand__services">Bitcoin education &amp; payment integration</div>
    </div>
  </section>
</main>
</body>
</html>
```